Web design project for exciting Australian start-up

Background
We are looking for a creative and talented web design artist to work alongside our market leading web developer.
• You will be required to create a modern and clean design theme for our website, incorporating selected rustic colour scheme elements for our exciting Australian start-up to operate within the coffee industry.
reoccurring work to be expected to flow to the successful designer.
Requirements
• c. 5 - 10 page website
• Landing page
• Log in/ out
• 404 template
• Typography is emphasised
• Please use either a) typemarrow.com, b) free web fonts, c) brindle fonts
• All design elements in vector format
• Preferably with icons for each header title(i.e. about us, how it works etc) but designer have free reign over how the site looks, so might not be applicable
• All pages to be responsive
• Down to eSlab resolution

High level visual design brief attached - additional pages to be worked from base design.

Design inspiration
• We would like to use design elements from the following sources:
http://www.zandrix.com/halcyon/ (Functionality)
Colour scheme refer to logo and complementary style guide

```html
<!DOCTYPE html>
<html lang="en">
<head>
<meta charset="utf-8">
<title>Brewmark – Wholesaler profile</title>
<link href="https://fonts.googleapis.com/css2?family=Cabin:wght@400;500;600;700&family=Roboto+Slab:wght@400;500&display=swap" rel="stylesheet">
<style>
:root{
  --red:#e33b3b;
  --orange:#f9a23a;
  --ink:#333333;
  --muted:#555555;
  --line:#dddddd;
  --panel:#f6f6f6;
  --dark:#4b4b4b;
  --footer:#e8e8e8;
  --white:#ffffff;
}
*{box-sizing:border-box;margin:0;padding:0}
html,body{width:1200px;height:989px;overflow:hidden;background:var(--white)}
body{font-family:"Cabin",sans-serif;color:var(--ink);position:relative}
.abs{position:absolute}
a{color:inherit;text-decoration:none}

.site-header{position:absolute;left:0;top:0;width:1200px;height:107px;border-bottom:1px solid #e6e6e6;box-shadow:0 2px 3px rgba(0,0,0,.05)}
.brand{left:160px;top:34px;display:flex;align-items:center;gap:10px;font-size:30px;font-weight:700;letter-spacing:1px;color:#222}
.brand-mark{width:30px;height:30px;border-radius:50%;background:var(--orange)}
.nav-item{top:0;height:107px;border-left:1px solid #eee;display:flex;flex-direction:column;align-items:center;justify-content:center;gap:8px;font-size:12px;color:var(--ink);text-transform:uppercase}
.nav-item:last-of-type{border-right:1px solid #eee}
.nav-item svg{width:20px;height:20px}
.btn{top:38px;height:31px;border-radius:2px;color:#fff;font-size:14px;display:flex;align-items:center;justify-content:center}
.btn-red{background:var(--red)}
.btn-orange{background:var(--orange)}

.profile-title{left:160px;top:140px;font-size:18px;font-weight:600;text-transform:uppercase;letter-spacing:.3px}
.profile-meta{left:160px;top:174px;font-size:13px;line-height:21px;color:var(--muted)}
.review-count{right:161px;top:132px;text-align:right;color:var(--red);font-size:25px;font-weight:500;line-height:1}
.review-label{right:161px;top:163px;color:var(--red);font-size:16px;font-weight:600}
.member-since{right:163px;top:185px;font-size:13px;color:var(--muted)}
.divider{left:160px;top:228px;width:877px;height:1px;background:var(--line)}

.tab{top:256px;height:46px;border:1px solid var(--line);background:#fff;display:flex;align-items:center;justify-content:center;font-size:14.5px;color:#222}
.tab.active{background:var(--panel);border-bottom:none;height:49px;color:var(--red);z-index:2}
.tab-panel{left:161px;top:304px;width:620px;height:334px;background:var(--panel);border:1px solid var(--line)}
.bean{top:59px;font-size:12px;line-height:21px;color:var(--muted)}
.bean strong{font-size:13px;color:#222;font-weight:600}
.bean-photo{top:33px;width:118px;height:102px;border-radius:2px;background:radial-gradient(circle at 55% 45%,#f1ebe3 0,#d9c8b8 35%,#6b3a33 70%,#2f3b2c 100%)}
.panel-rule{left:17px;top:171px;width:579px;height:1px;background:#e2e2e2}
.spec{top:230px;font-size:13px;line-height:22px;color:var(--muted);display:grid;grid-template-columns:155px auto}

.supply{left:829px;top:256px;width:210px;height:383px;background:var(--dark);color:#fff}
.supply h2{font-size:15px;font-weight:500;text-align:center;line-height:21px;margin:26px 20px 12px;text-transform:uppercase}
.supply-map{margin:0 12px;height:95px;border-radius:2px;background:linear-gradient(135deg,#e8dfc9,#d5cfb3 50%,#bcd3a5)}
.supply-stats{padding:20px 23px 0;font-size:12.5px;line-height:15.5px}
.supply-stats dt{font-weight:700}
.supply-stats dd{margin-bottom:15px}
.stars{display:flex;gap:7px;margin:4px 0 0 23px}
.stars svg{width:18px;height:18px}

.site-footer{left:0;top:684px;width:1200px;height:236px;background:var(--footer)}
.footer-col h3{font-family:"Roboto Slab",serif;font-weight:400;font-size:18px;letter-spacing:.5px;color:#222;text-transform:uppercase;margin-bottom:14px}
.footer-col li{list-style:none;font-size:14px;color:var(--muted);height:31px;display:flex;align-items:center;gap:20px}
.social-dot{width:11px;height:11px;background:#666;border-radius:2px}
.copyright{left:0;top:920px;width:1200px;height:69px;background:var(--dark);color:#fff;font-size:14px;display:flex;align-items:center;justify-content:center}
.copyright::before{content:"";position:absolute;left:160px;right:161px;top:5px;height:1px;background:#666}
</style>
</head>
<body>

<header class="site-header">
  <div class="abs brand"><span class="brand-mark"></span>BREWMARK</div>
  <a class="abs nav-item" style="left:423px;width:94px" href="#">
    <svg viewBox="0 0 20 20" fill="none" stroke="#f9a23a" stroke-width="1.3"><path d="M3 10 10 3l7 7M5 8.5V17h10V8.5M8.5 17v-5h3v5"/></svg>About Us</a>
  <a class="abs nav-item" style="left:517px;width:135px" href="#">
    <svg viewBox="0 0 20 20" fill="none" stroke="#888" stroke-width="1.2"><circle cx="8" cy="8" r="3"/><path d="M3 17c0-3 2-5 5-5s5 2 5 5M12 3h6v5h-6z"/></svg>How it works</a>
  <a class="abs nav-item" style="left:652px;width:66px" href="#">
    <svg viewBox="0 0 20 20" fill="none" stroke="#888" stroke-width="1.2"><rect x="4" y="5" width="4" height="12"/><rect x="11" y="3" width="4" height="14"/></svg>FAQ</a>
  <a class="abs btn btn-red" style="left:750px;width:118px" href="#">My Account</a>
  <a class="abs btn btn-orange" style="left:878px;width:75px" href="#">Login</a>
  <a class="abs btn btn-red" style="left:962px;width:76px" href="#">Sign up</a>
</header>

<main>
  <h1 class="abs profile-title">Hollow Bean Roasters</h1>
  <p class="abs profile-meta">Melbourne, Australia<br>[Wholesaler description]</p>
  <div class="abs review-count">[10]</div>
  <div class="abs review-label">Reviews</div>
  <div class="abs member-since">Member since [Feb, 2014</div>
  <div class="abs divider"></div>

  <a class="abs tab active" style="left:161px;width:122px" href="#">Our beans</a>
  <a class="abs tab" style="left:285px;width:127px" href="#">Accessories</a>
  <a class="abs tab" style="left:415px;width:127px" href="#">Machinery</a>
  <a class="abs tab" style="left:544px;width:115px" href="#">Training</a>
  <a class="abs tab" style="left:662px;width:118px" href="#">Promotions</a>

  <section class="abs tab-panel">
    <div class="abs bean" style="left:25px"><strong>Coffee bean XX</strong><br>The blend<br>[Insert blend description]</div>
    <div class="abs bean-photo" role="img" aria-label="Photo of a festive coffee mug" style="left:185px"></div>
    <div class="abs bean" style="left:327px"><strong>Coffee bean XX</strong><br>The blend<br>[Insert blend description]</div>
    <div class="abs bean-photo" role="img" aria-label="Photo of a festive coffee mug" style="left:478px"></div>
    <div class="abs panel-rule"></div>
    <dl class="abs spec" style="left:27px"><dt>Origin</dt><dd>: [xx]</dd><dt>Grind availability</dt><dd>: [xx]</dd></dl>
    <dl class="abs spec" style="left:405px"><dt>Origin</dt><dd>: [xx]</dd><dt>Grind availability</dt><dd>: [xx]</dd></dl>
  </section>

  <aside class="abs supply">
    <h2>Where we currently supply</h2>
    <div class="supply-map" role="img" aria-label="Street map of the supply area with a location pin"></div>
    <dl class="supply-stats">
      <dt>Tender response rate</dt><dd>[x]%</dd>
      <dt>Tender response time</dt><dd>[Within a few days]</dd>
      <dd style="margin-bottom:0">Wholesaler’s overall customer rating</dd>
    </dl>
    <div class="stars">
      <svg viewBox="0 0 20 20"><path fill="#f9a23a" d="M10 1l2.6 6 6.4.6-4.9 4.3 1.5 6.3L10 15l-5.6 3.2 1.5-6.3L1 7.6 7.4 7z"/></svg>
      <svg viewBox="0 0 20 20"><path fill="#f9a23a" d="M10 1l2.6 6 6.4.6-4.9 4.3 1.5 6.3L10 15l-5.6 3.2 1.5-6.3L1 7.6 7.4 7z"/></svg>
      <svg viewBox="0 0 20 20"><path fill="#f9a23a" d="M10 1l2.6 6 6.4.6-4.9 4.3 1.5 6.3L10 15l-5.6 3.2 1.5-6.3L1 7.6 7.4 7z"/></svg>
      <svg viewBox="0 0 20 20"><path fill="#e8e8e8" d="M10 1l2.6 6 6.4.6-4.9 4.3 1.5 6.3L10 15l-5.6 3.2 1.5-6.3L1 7.6 7.4 7z"/></svg>
      <svg viewBox="0 0 20 20"><path fill="#e8e8e8" d="M10 1l2.6 6 6.4.6-4.9 4.3 1.5 6.3L10 15l-5.6 3.2 1.5-6.3L1 7.6 7.4 7z"/></svg>
    </div>
  </aside>
</main>

<footer>
  <div class="abs site-footer">
    <div class="abs footer-col" style="left:295px;top:50px">
      <h3>Helpful info</h3>
      <ul><li>About Us</li><li>Media Enquiries</li><li>Terms &amp; Conditions</li><li>Privacy Policy</li></ul>
    </div>
    <div class="abs footer-col" style="left:541px;top:50px">
      <h3>Who we are</h3>
      <ul style="padding-left:8px"><li>How it works</li><li>FAQ</li><li>Contact us</li></ul>
    </div>
    <div class="abs footer-col" style="left:798px;top:50px">
      <h3>Join us on</h3>
      <ul style="padding-left:2px">
        <li><span style="width:80px">Chatterbox</span><span class="social-dot"></span></li>
        <li><span style="width:80px">Chirpline</span><span class="social-dot"></span></li>
        <li><span style="width:80px">Workloop</span><span class="social-dot"></span></li>
        <li><span style="width:80px">Reelcast</span><span class="social-dot"></span></li>
      </ul>
    </div>
  </div>
  <div class="abs copyright">Copyright © 2014 Brewmark</div>
</footer>

</body>
</html>
```